47 on Birch Apartment Mailer to Competition

I need a postcard mailer designed that will be promoting a new apartment building in downtown Rochester NY. The postcards are being mailed to other apartment communities the we are in direct competition with. I have enclosed a bunch of info to guide you.

Target Market(s)

Other communities in the market

Industry/Entity Type

Property Management

Requirements
Must have
• Exterior rendering, features. Fit standard postcard, colors similar to enclosed, grey, white coral
Nice to have
• Interior Pictures

```html
<!DOCTYPE html>
<html lang="en">
<head>
<meta charset="utf-8">
<title>47 on Birch – Apartment Mailer</title>
<link href="https://fonts.googleapis.com/css2?family=Fira+Sans+Extra+Condensed:wght@400;700&display=swap" rel="stylesheet">
<style>
  :root {
    --coral: #e8413a;
    --maroon: #4d1515;
    --ink: #1f1a1a;
    --white: #ffffff;
  }
  html, body { margin: 0; padding: 0; overflow: hidden; background: var(--white); }
  .mailer {
    position: relative;
    width: 850px;
    height: 1200px;
    overflow: hidden;
    background: var(--white);
    font-family: "Fira Sans Extra Condensed", "Arial Narrow", sans-serif;
  }
  .rendering {
    position: absolute; left: 0; top: 0; width: 850px; height: 740px;
    background:
      linear-gradient(90deg, rgba(60,90,60,0.55) 0%, rgba(60,90,60,0) 14%),
      linear-gradient(90deg, rgba(0,0,0,0) 48%, #c9ced4 50%, #dfe3e6 75%, #aeb4ba 90%, rgba(0,0,0,0) 97%),
      linear-gradient(180deg, #4f6f8c 0%, #8fa1ad 28%, #d9a47c 40%, #9a8f86 52%, #6f6a66 75%, #4a4644 100%);
  }
  .shapes { position: absolute; left: 0; top: 0; }
  .brand-square {
    position: absolute; left: 102px; top: 40px; width: 84px; height: 84px;
    background: var(--maroon);
  }
  .brand-name {
    position: absolute; left: 0; top: 182px; width: 288px; text-align: center;
    font-weight: 400; font-size: 34px; line-height: 40px; letter-spacing: 2px;
    color: var(--maroon); text-transform: uppercase; white-space: nowrap;
  }
  .section {
    position: absolute; left: 0; width: 850px; text-align: center;
  }
  .section h2 {
    margin: 0; font-weight: 700; font-size: 35px; line-height: 40px; color: var(--coral);
    text-transform: uppercase; letter-spacing: 0.2px;
  }
  .section p {
    margin: 0; font-size: 21px; line-height: 33px; white-space: nowrap;
  }
  .community { top: 656px; color: var(--ink); }
  .community h2 { margin-bottom: 4px; }
  .community p { line-height: 33px; }
  .home { top: 850px; color: var(--white); }
  .home h2 { margin-bottom: 4px; }
  .home p { line-height: 35.5px; }
  .plans { top: 1054px; color: var(--ink); }
  .plans h2 { margin-bottom: 4px; }
  .plans p { line-height: 35px; }
  .sep {
    display: inline-block; width: 3px; height: 25px; background: var(--coral);
    vertical-align: -6px; margin: 0 4px;
  }
</style>
</head>
<body>
<main class="mailer">
  <div class="rendering" role="img" aria-label="Exterior rendering of the glass-fronted apartment tower at dusk among downtown buildings, with residents visible in the lit units"></div>

  <svg class="shapes" width="850" height="1200" viewBox="0 0 850 1200" aria-hidden="true">
    <path d="M0 730 Q425 540 850 730 L850 1200 L0 1200 Z" fill="var(--white)"/>
    <path d="M0 730 Q425 540 850 730" fill="none" stroke="var(--coral)" stroke-width="6"/>
    <path d="M0 922 Q425 760 850 922 L850 1128 Q425 966 0 1128 Z" fill="var(--maroon)"/>
    <path d="M0 922 Q425 760 850 922" fill="none" stroke="var(--coral)" stroke-width="5"/>
    <path d="M0 1128 Q425 966 850 1128" fill="none" stroke="var(--coral)" stroke-width="5"/>
    <circle cx="104" cy="78" r="212" fill="var(--white)" stroke="var(--maroon)" stroke-width="9"/>
  </svg>

  <div class="brand-square" aria-hidden="true"></div>
  <div class="brand-name">47 on Birch</div>

  <section class="section community">
    <h2>Community Features</h2>
    <p>Rooftop patio<span class="sep"></span>24 Hour Fitness<span class="sep"></span>5x10 Storage Unit<span class="sep"></span>High Speed Internet and cable Included</p>
    <p>Heat and A/C Included<span class="sep"></span>Parking Available, One Spot Included</p>
    <p>Modern Security with Controlled Access and key Fobs<span class="sep"></span>Amazing Views<span class="sep"></span>Den Available</p>
    <p>24 Hour Maintenance</p>
  </section>

  <section class="section home">
    <h2>Home Features</h2>
    <p>Floor to Ceiling Operable Windows<span class="sep"></span>W/D In Unit<span class="sep"></span>LED Lighting<span class="sep"></span>Hardwood Flooring</p>
    <p>Automatic Window Treatments<span class="sep"></span>Granite Countertops<span class="sep"></span>Undermount Sinks</p>
    <p>Tile backsplash<span class="sep"></span>Walk-In Closets Available<span class="sep"></span>Open Floor Plans</p>
    <p>Contemporary Cabinetry and Fixtures</p>
  </section>

  <section class="section plans">
    <h2>Floor Plans</h2>
    <p>1 Bedroom, 1 Bedroom with Den, and 2 Bedroom 2 Bath Available</p>
    <p>$1400 to $3300<span class="sep"></span>775 to 1677 sq. ft.</p>
  </section>
</main>
</body>
</html>
```